Tallwick Home Services Web Site

Design Web site with 3-4 pages: Home, About Us, Services and Order form / Schedule Appointment (which will likely be link to Method App and Quickbooks integration.)
Services include: Dryer Vent Cleaning, AC Cleaning, Difficult-to-Reach Light Bulb replacement, Wood Repair and Home Maintenance Plans including Fire Safety Checks and Filter Replacement.

Target Market(s)

Luxury Home Owners, Professionals (Dr's/lawyers) and Seniors

Industry/Entity Type

Home Maintenance

Coding

Coded - Design and coding required

Requirements
Must have
• Tagline - Where Home Maintenance is Elementary

```html
<!DOCTYPE html>
<html lang="en">
<head>
<meta charset="utf-8">
<title>Tallwick Home Services</title>
<link href="https://fonts.googleapis.com/css2?family=Poppins:wght@400;500;600;700&display=swap" rel="stylesheet">
<style>
:root{
  --gold:#e2a72a;
  --gold-pale:#fcf3df;
  --ink:#262626;
  --text:#5f5f5f;
  --muted:#8a8a8a;
  --heading:#555;
  --band:#f3f3f3;
  --slate:#6c6c73;
  --white:#fff;
}
*{box-sizing:border-box;margin:0;padding:0}
html,body{width:1200px;height:4083px;overflow:hidden}
body{font-family:'Poppins',sans-serif;color:var(--ink);background:var(--white);position:relative}
.abs{position:absolute}
.btn{position:absolute;display:flex;align-items:center;justify-content:center;background:var(--gold);color:var(--white);font-weight:600;font-size:15px;border-radius:30px;text-transform:uppercase;letter-spacing:.2px}
.section-title{position:absolute;left:0;width:1200px;text-align:center;font-size:45px;font-weight:500;color:var(--heading);letter-spacing:1px}
.section-title::after{content:"";display:block;width:62px;height:3px;background:var(--gold);margin:2px auto 0}

/* header */
.header{position:absolute;left:0;top:0;width:1200px;height:140px;background:var(--white);z-index:3}
.logo-tab{position:absolute;left:71px;top:0;width:286px;height:198px;background:var(--white);clip-path:polygon(0 0,100% 0,100% 72%,82% 100%,18% 100%,0 72%);z-index:4;display:flex;flex-direction:column;align-items:center;justify-content:center;padding-top:10px;color:var(--gold);font-weight:600}
.logo-mark{width:44px;height:44px;border-radius:50%;background:var(--gold);margin-bottom:12px}
.logo-name{font-size:30px;letter-spacing:3px;line-height:1}
.logo-sub{font-size:15px;letter-spacing:1px;margin-top:6px}
.social{position:absolute;width:34px;height:34px;border-radius:50%;background:var(--gold-pale)}
.social::after{content:"";position:absolute;left:12px;top:12px;width:10px;height:10px;border-radius:50%;background:var(--gold)}
.nav{position:absolute;top:90px;left:421px;display:flex;gap:30px;font-size:14.5px;font-weight:500;color:#444;text-transform:uppercase}
.nav .active{color:var(--gold);border-bottom:2px solid var(--gold);padding-bottom:2px}
.call-icon{position:absolute;left:869px;top:77px;width:46px;height:46px;border-radius:50%;background:var(--white);box-shadow:0 4px 12px rgba(0,0,0,.12);display:flex;align-items:center;justify-content:center}
.call{position:absolute;left:932px;top:79px;line-height:1.2}
.call small{display:block;font-size:11px;font-weight:600}
.call span{font-size:18px;color:#444}

/* hero */
.hero-photo{position:absolute;left:0;top:140px;width:1200px;height:650px;background:linear-gradient(100deg,#f6f6f6 0%,#ececec 45%,#d9d7d2 62%,#c9c4bb 78%,#e7e7e7 100%);clip-path:polygon(0 0,100% 0,100% 82%,50% 100%,0 72%)}
.hero-title{position:absolute;left:111px;top:250px;font-size:49px;font-weight:700;line-height:57px;letter-spacing:1px;color:var(--ink);text-transform:uppercase}
.hero-sub{position:absolute;left:111px;top:428px;font-size:22px;line-height:31px;color:var(--ink)}
.dot{position:absolute;left:49px;width:12px;height:12px;border-radius:50%;border:1.5px solid #888}
.dot.on{background:var(--gold);border-color:var(--gold)}

/* services */
.card{position:absolute;width:317px;height:458px;background:var(--white);border-radius:14px;box-shadow:0 4px 18px rgba(0,0,0,.09);overflow:hidden;text-align:center}
.card .photo{height:239px}
.card h3{font-size:18px;font-weight:500;margin-top:26px;line-height:28px;padding:0 20px}
.card p{font-size:16px;line-height:24px;color:var(--text);margin-top:8px;padding:0 28px}
.card .more{position:absolute;left:82px;bottom:26px;width:154px;height:47px;border-radius:30px;background:var(--gold-pale);color:var(--gold);font-weight:600;font-size:15px;display:flex;align-items:center;justify-content:center}
.card .more.solid{background:var(--gold);color:var(--white)}

/* about */
.about{position:absolute;left:0;top:2021px;width:1200px;height:580px;background:var(--band)}
.ring{position:absolute;border-radius:50%;border:2px solid #e4e4e4}
.about-photo{position:absolute;left:135px;top:2089px;width:444px;height:444px;border-radius:50%;background:radial-gradient(circle at 40% 45%,#efece6,#d6d0c6 70%,#c3bcb1)}
.about h2{position:absolute;left:650px;top:98px;font-size:45px;font-weight:500;color:var(--heading);letter-spacing:1px}
.about h2::after{content:"";display:block;width:62px;height:3px;background:var(--gold);margin-top:2px}
.about p{position:absolute;left:650px;width:439px;font-size:16px;line-height:25.5px;color:var(--text);text-align:justify}

/* why */
.why{position:absolute;left:0;top:2601px;width:1200px;height:547px;background:linear-gradient(180deg,#707077,#65656c)}
.why .section-title{color:var(--white);top:62px}
.feature{position:absolute;width:220px;text-align:center;color:var(--white)}
.feature .icon{width:104px;height:104px;border-radius:50%;background:var(--gold);margin:0 auto;position:relative;display:flex;align-items:center;justify-content:center}
.feature .icon::before{content:"";position:absolute;inset:7px;border-radius:50%;border:2px dashed rgba(255,255,255,.75)}
.feature h4{font-size:17px;font-weight:600;line-height:24px;margin-top:22px;text-transform:uppercase}
.feature p{font-size:16px;line-height:24px;margin-top:10px}

/* testimonials */
.quote{position:absolute;top:3347px;width:312px;height:254px;background:var(--white);border-radius:12px;box-shadow:0 4px 18px rgba(0,0,0,.09);padding:26px 22px}
.stars{display:flex;gap:3px}
.quote p{font-size:14.5px;line-height:22px;color:var(--text);margin-top:14px}
.quote .who{position:absolute;left:22px;right:22px;bottom:24px;border-top:1px solid #ddd;padding-top:18px;display:flex;align-items:center;gap:20px}
.avatar{width:56px;height:56px;border-radius:50%;background:linear-gradient(135deg,#e8ddd0,#c7b8a5)}
.who b{display:block;font-size:15px;font-weight:600;text-transform:uppercase}
.who small{font-size:12px;color:var(--muted)}
.arrow{position:absolute;top:3457px;width:34px;height:34px;border-radius:50%;display:flex;align-items:center;justify-content:center}

/* footer */
.foot-logo{position:absolute;left:111px;top:3840px;width:175px;text-align:center;color:var(--gold);font-weight:600}
.foot-h{position:absolute;top:3776px;font-size:17px;font-weight:500;color:#444;text-transform:uppercase}
.links{position:absolute;left:347px;top:3818px;list-style:none;font-size:15px;color:#444}
.links li{height:31px;display:flex;align-items:center;gap:18px}
.bullet{width:13px;height:13px;border-radius:50%;background:var(--gold);position:relative}
.bullet::after{content:"";position:absolute;left:4px;top:3.5px;border-left:5px solid #fff;border-top:3px solid transparent;border-bottom:3px solid transparent}
.contact{position:absolute;left:567px;font-size:12.5px;line-height:20px;color:#444}
.contact b{display:block;font-size:14px;font-weight:600}
.ci{position:absolute;left:534px}
.news{position:absolute;left:778px;top:3820px;width:309px;height:48px;border-radius:30px;background:var(--white);box-shadow:0 3px 12px rgba(0,0,0,.12)}
.news span{position:absolute;left:18px;top:14px;font-size:13px;color:#666}
.news .btn{left:203px;top:4px;width:102px;height:40px;font-size:13px}
.rule{position:absolute;left:111px;top:4021px;width:978px;height:1px;background:#ddd}
.copy{position:absolute;left:418px;top:4038px;font-size:13.5px;color:#444}
.fs{position:absolute;top:4033px;width:38px;height:38px;border-radius:50%;background:var(--white);box-shadow:0 2px 8px rgba(0,0,0,.14)}
.fs.on{background:var(--gold)}
</style>
</head>
<body>

<header class="header">
  <div class="social" style="left:674px;top:21px"></div>
  <div class="social" style="left:719px;top:21px"></div>
  <div class="social" style="left:764px;top:21px"></div>
  <div class="btn" style="left:832px;top:16px;width:257px;height:44px;font-size:14px">Schedule an Appointment</div>
  <nav class="nav"><span class="active">Home</span><span>About Us</span><span>Our Services</span><span>Contact Us</span></nav>
  <div class="call-icon"><svg width="18" height="18" viewBox="0 0 24 24"><path fill="#e2a72a" d="M6.6 10.8a15 15 0 0 0 6.6 6.6l2.2-2.2c.3-.3.7-.4 1-.2 1.1.4 2.3.6 3.6.6.6 0 1 .4 1 1V20c0 .6-.4 1-1 1A17 17 0 0 1 3 4c0-.6.4-1 1-1h3.5c.6 0 1 .4 1 1 0 1.3.2 2.5.6 3.6.1.3 0 .7-.2 1z"/></svg></div>
  <div class="call"><small>CALL US:</small><span>+1 (555) 014 2290</span></div>
</header>
<div class="logo-tab"><div class="logo-mark"></div><div class="logo-name">TALLWICK</div><div class="logo-sub">HOME SERVICES</div></div>

<!-- hero -->
<div class="hero-photo" role="img" aria-label="Smiling handyman in checked shirt and apron holding a clipboard in a bright kitchen"></div>
<svg class="abs" style="left:0;top:600px" width="1200" height="200" viewBox="0 0 1200 200">
  <polygon points="300,94 600,189 826,113 600,168" fill="#e2a72a"/>
</svg>
<h1 class="hero-title">Where Home<br>Maintenance is<br>Elementary</h1>
<p class="hero-sub">Professional maintenance services that<br>keep your home safe, clean, and efficient.</p>
<div class="btn" style="left:111px;top:512px;width:274px;height:46px">Schedule an Appointment</div>
<div class="dot" style="top:351px"></div>
<div class="dot on" style="top:375px"></div>
<div class="dot" style="top:399px"></div>
<div class="dot" style="top:423px"></div>

<!-- services -->
<h2 class="section-title" style="top:862px">OUR SERVICES</h2>

<div class="card" style="left:103px;top:964px">
  <div class="photo" role="img" aria-label="Dryer vent duct full of lint" style="background:linear-gradient(135deg,#e9e9e9,#a9a9a9 60%,#d6d6d6)"></div>
  <h3>DRYER VENT CLEANING</h3>
  <p>Sed ut perspiciatis unde omnis iste natus error sit voluptatem accusantium.</p>
  <div class="more">LEARN MORE</div>
</div>
<div class="card" style="left:441px;top:964px">
  <div class="photo" role="img" aria-label="Technician cleaning a wall-mounted air conditioner" style="background:linear-gradient(135deg,#6d6a66,#c9c5bd 55%,#eeeeee)"></div>
  <h3>AC CLEANING</h3>
  <p>Sed ut perspiciatis unde omnis iste natus error sit voluptatem accusantium.</p>
  <div class="more solid">LEARN MORE</div>
</div>
<div class="card" style="left:780px;top:964px">
  <div class="photo" role="img" aria-label="Worker on a ladder replacing a ceiling light" style="background:linear-gradient(180deg,#f1f0ee,#d3cdc4 70%,#b9a58a)"></div>
  <h3>LIGHT BULB REPLACEMENT</h3>
  <p>Sed ut perspiciatis unde omnis iste natus error sit voluptatem accusantium.</p>
  <div class="more">LEARN MORE</div>
</div>

<div class="card" style="left:103px;top:1447px">
  <div class="photo" role="img" aria-label="Brush applying finish to a wooden plank" style="background:linear-gradient(135deg,#3d2c22,#8a6a4f 50%,#c9b8a4)"></div>
  <h3>WOOD REPAIR</h3>
  <p>Sed ut perspiciatis unde omnis iste natus error sit voluptatem accusantium.</p>
  <div class="more">LEARN MORE</div>
</div>
<div class="card" style="left:441px;top:1447px">
  <div class="photo" role="img" aria-label="Contractor reviewing plans with homeowners" style="background:linear-gradient(135deg,#b78d5c,#d8b98e 50%,#9b7a55)"></div>
  <h3>HOME MAINTENANCE PLANS</h3>
  <p>Sed ut perspiciatis unde omnis iste natus error sit voluptatem accusantium.</p>
  <div class="more">LEARN MORE</div>
</div>
<div class="card" style="left:780px;top:1447px">
  <div class="photo" role="img" aria-label="Hands fitting a smoke detector to a ceiling" style="background:linear-gradient(180deg,#f3f3f3,#d7d9dc 65%,#8d9095)"></div>
  <h3>FIRE SAFETY CHECKS AND FILTER REPLACEMENT</h3>
  <p>Sed ut perspiciatis unde omnis iste natus errorea.</p>
  <div class="more">LEARN MORE</div>
</div>

<!-- about -->
<section class="about">
  <h2>ABOUT US</h2>
  <p style="top:180px">Lorem ipsum dolor sit amet, consectetur adipiscing elit, sed do eiusmod tempor incididunt ut labore et dolore magna aliqua. Ut enim ad minim veniam, quis nostrud exercitation ullamco laboris nisi ut aliquip ex ea commodo consequat.</p>
  <p style="top:321px">Lorem ipsum dolor sit amet, consectetur adipiscing elit, sed do eiusmod tempor incididunt ut labore et dolore magna aliqua.</p>
  <div class="btn" style="left:650px;top:428px;width:154px;height:44px">Learn More</div>
</section>
<div class="ring" style="left:111px;top:2065px;width:492px;height:492px"></div>
<div class="abs" style="left:475px;top:2094px;width:10px;height:10px;border-radius:50%;background:var(--gold)"></div>
<div class="abs" style="left:220px;top:2513px;width:10px;height:10px;border-radius:50%;background:var(--gold)"></div>
<div class="about-photo" role="img" aria-label="Couple sitting on the floor of their new home beside moving boxes"></div>

<!-- why choose us -->
<section class="why" role="region" aria-label="Why choose us">
  <h2 class="section-title">WHY CHOOSE US</h2>
  <div class="feature" style="left:114px;top:160px">
    <div class="icon"><svg width="44" height="40" viewBox="0 0 44 40"><circle cx="22" cy="12" r="7" fill="#fff"/><path d="M8 38c0-9 6-15 14-15s14 6 14 15z" fill="#fff"/></svg></div>
    <h4>20+ Years of<br>Experience</h4>
    <p>Sed ut perspiciatis undeo iste natus error sit voluptatem accusantium doloremque.</p>
  </div>
  <div class="feature" style="left:364px;top:207px">
    <div class="icon"><svg width="38" height="38" viewBox="0 0 24 24"><path fill="#fff" d="M6.6 10.8a15 15 0 0 0 6.6 6.6l2.2-2.2c.3-.3.7-.4 1-.2 1.1.4 2.3.6 3.6.6.6 0 1 .4 1 1V20c0 .6-.4 1-1 1A17 17 0 0 1 3 4c0-.6.4-1 1-1h3.5c.6 0 1 .4 1 1 0 1.3.2 2.5.6 3.6.1.3 0 .7-.2 1z"/></svg></div>
    <h4>Emergency Services<br>Available 24/7</h4>
    <p>Sed ut perspiciatis undeo iste natus error sit voluptatem accusantium doloremque.</p>
  </div>
  <div class="feature" style="left:616px;top:160px">
    <div class="icon"><svg width="40" height="40" viewBox="0 0 40 40"><circle cx="20" cy="20" r="17" fill="none" stroke="#fff" stroke-width="3"/><path d="M12 20l6 6 11-12" fill="none" stroke="#fff" stroke-width="3.5" stroke-linecap="round" stroke-linejoin="round"/></svg></div>
    <h4>Trusted by<br>Industry Leaders</h4>
    <p>Sed ut perspiciatis undeo iste natus error sit voluptatem accusantium doloremque.</p>
  </div>
  <div class="feature" style="left:866px;top:207px">
    <div class="icon"><svg width="40" height="40" viewBox="0 0 40 40"><rect x="8" y="6" width="24" height="30" rx="3" fill="none" stroke="#fff" stroke-width="3"/><path d="M14 17h12M14 23h12M14 29h8" stroke="#fff" stroke-width="3" stroke-linecap="round"/></svg></div>
    <h4>End-to-End<br>Project Management</h4>
    <p>Sed ut perspiciatis undeo iste natus error sit voluptatem accusantium doloremque.</p>
  </div>
</section>

<!-- testimonials -->
<h2 class="section-title" style="top:3244px">TESTIMONIALS</h2>
<svg width="0" height="0" style="position:absolute"><defs><polygon id="star" points="6,0 7.8,4 12,4.4 8.8,7.2 9.7,11.5 6,9.3 2.3,11.5 3.2,7.2 0,4.4 4.2,4" fill="#e2a72a"/></defs></svg>

<div class="arrow" style="left:35px;background:#d9d9d9"><svg width="14" height="14" viewBox="0 0 14 14"><path d="M9 2L4 7l5 5" fill="none" stroke="#fff" stroke-width="2.5"/></svg></div>
<div class="arrow" style="left:1130px;background:var(--gold)"><svg width="14" height="14" viewBox="0 0 14 14"><path d="M5 2l5 5-5 5" fill="none" stroke="#fff" stroke-width="2.5"/></svg></div>

<div class="quote" style="left:111px">
  <div class="stars"><svg width="12" height="12"><use href="#star"/></svg><svg width="12" height="12"><use href="#star"/></svg><svg width="12" height="12"><use href="#star"/></svg><svg width="12" height="12"><use href="#star"/></svg><svg width="12" height="12"><use href="#star"/></svg></div>
  <p>Lorem ipsum dolor sit amet, consect adipiscing elit, sed do eiusmod temp incididunt ut labore et dolore magna aliqua ut enim ad minimea.</p>
  <div class="who"><div class="avatar" role="img" aria-label="Customer portrait"></div><div><b>Mara Quinlan,</b><small>1 year ago</small></div></div>
</div>
<div class="quote" style="left:444px">
  <div class="stars"><svg width="12" height="12"><use href="#star"/></svg><svg width="12" height="12"><use href="#star"/></svg><svg width="12" height="12"><use href="#star"/></svg><svg width="12" height="12"><use href="#star"/></svg><svg width="12" height="12"><use href="#star"/></svg></div>
  <p>Lorem ipsum dolor sit amet, consect adipiscing elit, sed do eiusmod temp incididunt ut labore et dolore magna aliqua ut enim ad minimea.</p>
  <div class="who"><div class="avatar" role="img" aria-label="Customer portrait" style="background:linear-gradient(135deg,#d8d2c8,#8e8376)"></div><div><b>Devon Hale,</b><small>1 year ago</small></div></div>
</div>
<div class="quote" style="left:777px">
  <div class="stars"><svg width="12" height="12"><use href="#star"/></svg><svg width="12" height="12"><use href="#star"/></svg><svg width="12" height="12"><use href="#star"/></svg><svg width="12" height="12"><use href="#star"/></svg><svg width="12" height="12"><use href="#star"/></svg></div>
  <p>Lorem ipsum dolor sit amet, consect adipiscing elit, sed do eiusmod temp incididunt ut labore et dolore magna aliqua ut enim ad minimea.</p>
  <div class="who"><div class="avatar" role="img" aria-label="Customer portrait"></div><div><b>Mara Quinlan,</b><small>1 year ago</small></div></div>
</div>

<!-- footer -->
<div class="abs" style="left:0;top:3712px;width:1200px;height:1px;background:#eee"></div>
<div class="foot-logo"><div class="logo-mark" style="margin:0 auto 12px"></div><div style="font-size:27px;letter-spacing:3px;line-height:1">TALLWICK</div><div style="font-size:13px;letter-spacing:1px;margin-top:6px">HOME SERVICES</div></div>

<div class="foot-h" style="left:347px">Quick Links</div>
<ul class="links">
  <li><i class="bullet"></i>Home</li>
  <li><i class="bullet"></i>About Us</li>
  <li><i class="bullet"></i>Our Services</li>
  <li><i class="bullet"></i>Contact Us</li>
  <li><i class="bullet"></i>Privacy Policy</li>
  <li><i class="bullet"></i>Terms Of Use</li>
</ul>

<div class="foot-h" style="left:534px">Contact Info</div>
<svg class="ci" style="top:3820px" width="12" height="16" viewBox="0 0 12 16"><path d="M6 0a6 6 0 0 0-6 6c0 4.5 6 10 6 10s6-5.5 6-10a6 6 0 0 0-6-6zm0 8.5A2.5 2.5 0 1 1 6 3.5a2.5 2.5 0 0 1 0 5z" fill="#e2a72a"/></svg>
<div class="contact" style="top:3818px"><b>ADDRESS:</b>465, Lorum Ipsum Dolore,<br>United State</div>
<svg class="ci" style="top:3900px" width="14" height="14" viewBox="0 0 24 24"><path fill="#e2a72a" d="M6.6 10.8a15 15 0 0 0 6.6 6.6l2.2-2.2c.3-.3.7-.4 1-.2 1.1.4 2.3.6 3.6.6.6 0 1 .4 1 1V20c0 .6-.4 1-1 1A17 17 0 0 1 3 4c0-.6.4-1 1-1h3.5c.6 0 1 .4 1 1 0 1.3.2 2.5.6 3.6.1.3 0 .7-.2 1z"/></svg>
<div class="contact" style="top:3896px"><b>PHONE:</b>+1 (555) 014 2290</div>
<svg class="ci" style="top:3960px" width="15" height="11" viewBox="0 0 15 11"><rect width="15" height="11" rx="1.5" fill="#e2a72a"/><path d="M1 1l6.5 5L14 1" fill="none" stroke="#fff" stroke-width="1.4"/></svg>
<div class="contact" style="top:3954px"><b>EMAIL:</b>info@tallwickhomeservices.com</div>

<div class="foot-h" style="left:778px">Newsletter Signup</div>
<div class="news"><span>Email Address</span><div class="btn">Sign Up</div></div>

<div class="rule"></div>
<div class="copy">© 2025 Tallwick Home Services &nbsp;-&nbsp; All Rights Reserved</div>
<div class="fs on" style="left:960px" aria-label="Social link"></div>
<div class="fs" style="left:1004px" aria-label="Social link"></div>
<div class="fs" style="left:1048px" aria-label="Social link"></div>

</body>
</html>
```